Lumavento business card

We need a modern business card - With our 4 colors - See web: www.lumavento.dk

I have attached logo and som old business Cards we have - Lets Make the new ones shine...:-) -

Industry/Entity Type

Business

Requirements
Must have
• the logo with lumavento only,

```html
<!DOCTYPE html>
<html lang="da">
<head>
<meta charset="utf-8">
<title>Lumavento business card</title>
<link href="https://fonts.googleapis.com/css2?family=Source+Sans+3:wght@400;600&display=swap" rel="stylesheet">
<style>
  :root {
    --orange: #f08a24;
    --lime: #a6c832;
    --pink: #e4138c;
    --purple: #6f2877;
    --ink: #333333;
    --paper: #ffffff;
    --backdrop: #e9e6e3;
  }
  * { margin: 0; padding: 0; box-sizing: border-box; }
  html, body { width: 1200px; height: 900px; overflow: hidden; }
  body {
    position: relative;
    background: var(--backdrop);
    font-family: "Source Sans 3", sans-serif;
  }
  .card { position: absolute; overflow: hidden; box-shadow: 0 4px 14px rgba(0,0,0,.12); }

  /* Front */
  .card-front { left: 238px; top: 60px; width: 555px; height: 344px; background: var(--paper); }
  .brand-dot { position: absolute; left: 262px; top: 58px; width: 34px; height: 34px; border-radius: 50%; background: var(--lime); }
  .brand-name {
    position: absolute; left: 0; width: 558px; top: 122px; text-align: center;
    font-size: 17px; font-weight: 400; letter-spacing: 2px; color: var(--ink);
  }
  .brand-rule { position: absolute; left: 173px; top: 152px; width: 200px; height: 2px; background: var(--lime); }
  .tagline { position: absolute; left: 0; width: 558px; top: 165px; text-align: center; font-size: 12px; color: var(--ink); }
  .person { position: absolute; right: 290px; top: 211px; text-align: right; }
  .person-name { font-size: 21px; font-weight: 600; color: var(--purple); line-height: 1.2; }
  .person-title { font-size: 14px; color: var(--orange); margin-top: 2px; }
  .contacts { position: absolute; left: 287px; top: 201px; list-style: none; }
  .contacts li { display: flex; align-items: center; height: 23.5px; font-size: 14.5px; color: var(--orange); }
  .contacts svg { width: 12px; height: 12px; margin-right: 13px; fill: var(--purple); }
  .address-band {
    position: absolute; left: 0; bottom: 0; width: 100%; height: 48px; background: var(--purple);
    display: flex; align-items: center; justify-content: center;
    color: var(--paper); font-size: 15px;
  }

  /* Back */
  .card-back {
    left: 457px; top: 518px; width: 560px; height: 342px;
    background: linear-gradient(to bottom, var(--orange) 0%, var(--lime) 28%, var(--lime) 36%, var(--pink) 70%, var(--pink) 80%, var(--purple) 100%);
  }
  .back-brand { position: absolute; left: 0; top: 150px; width: 100%; display: flex; align-items: center; justify-content: center; gap: 14px; }
  .back-dot { width: 36px; height: 36px; border-radius: 50%; background: var(--paper); }
  .back-name { font-size: 34px; font-weight: 400; letter-spacing: 3px; color: var(--paper); }
</style>
</head>
<body>
  <section class="card card-front" aria-label="Business card front">
    <div class="brand-dot"></div>
    <div class="brand-name">lumavento</div>
    <div class="brand-rule"></div>
    <div class="tagline">Medier til unge</div>

    <div class="person">
      <div class="person-name">Sigrid Holmvang</div>
      <div class="person-title">Salgsdirektor</div>
    </div>

    <ul class="contacts">
      <li><svg viewBox="0 0 24 24" aria-hidden="true"><path d="M6.6 10.8a15.1 15.1 0 0 0 6.6 6.6l2.2-2.2c.3-.3.7-.4 1-.2 1.1.4 2.3.6 3.6.6.6 0 1 .4 1 1V20c0 .6-.4 1-1 1A17 17 0 0 1 3 4c0-.6.4-1 1-1h3.5c.6 0 1 .4 1 1 0 1.3.2 2.5.6 3.6.1.3 0 .7-.2 1z"/></svg>+45 20 30 40 51</li>
      <li><svg viewBox="0 0 24 24" aria-hidden="true"><path d="M2 5h20v14H2zm2 2v.5l8 5 8-5V7l-8 5z"/></svg>sh@lumavento.dk</li>
      <li><svg viewBox="0 0 24 24" aria-hidden="true"><circle cx="12" cy="12" r="10"/></svg>www.lumavento.dk</li>
    </ul>

    <div class="address-band">Kastanievej 14 - 2000 Frederiksberg - Tlf. 33 12 45 67</div>
  </section>

  <section class="card card-back" aria-label="Business card back">
    <div class="back-brand">
      <div class="back-dot"></div>
      <div class="back-name">lumavento</div>
    </div>
  </section>
</body>
</html>
```